Marwick Law Letterhead

We need a new letterhead design for a Law Firm. The address for the law firm is 1475 Calloway Street, Suite 210, Houston, Texas 77041. Phone Number: 832-361-9027; Fax Number: 832-614-7359. The logo is uploaded to the project.

```html
<!DOCTYPE html>
<html lang="en">
<head>
<meta charset="utf-8">
<title>Marwick Law Letterhead</title>
<link href="https://fonts.googleapis.com/css2?family=Montserrat:wght@400;500;600&display=swap" rel="stylesheet">
<style>
  :root {
    --backdrop: #e9e9eb;
    --paper: #ffffff;
    --red-bright: #e01b25;
    --red-deep: #6e000c;
    --navy: #1b2b5a;
    --ink: #1c1c1c;
    --muted: #333333;
  }
  html, body {
    margin: 0;
    width: 1200px;
    height: 960px;
    overflow: hidden;
    background: var(--backdrop);
    font-family: "Montserrat", Arial, sans-serif;
  }
  .letterhead {
    position: absolute;
    left: 280px;
    top: 24px;
    width: 640px;
    height: 910px;
    background: var(--paper);
    box-shadow: 0 6px 24px rgba(0,0,0,0.12);
    overflow: hidden;
    color: var(--ink);
  }
  .header-sweep {
    position: absolute;
    left: 0;
    top: 0;
    width: 640px;
    height: 270px;
  }
  .brand {
    position: absolute;
    left: 300px;
    top: 140px;
    display: flex;
    align-items: center;
    gap: 10px;
  }
  .brand-mark {
    width: 30px;
    height: 30px;
    background: var(--navy);
  }
  .brand-name {
    font-size: 26px;
    font-weight: 600;
    color: var(--navy);
    letter-spacing: 0.5px;
  }
  .recipient {
    position: absolute;
    left: 58px;
    top: 280px;
    font-size: 11px;
    line-height: 15px;
  }
  .letter-body {
    position: absolute;
    left: 58px;
    top: 350px;
    width: 520px;
    font-size: 10.5px;
    line-height: 14.5px;
    color: var(--muted);
  }
  .letter-body p { margin: 0 0 14px; }
  .closing {
    position: absolute;
    left: 58px;
    top: 760px;
    font-size: 12px;
  }
  .signature {
    display: block;
    margin-top: 6px;
    width: 100px;
    height: 26px;
    background: linear-gradient(90deg, rgba(28,28,28,0.15), rgba(28,28,28,0.05));
    border-radius: 4px;
  }
  .contact-bar {
    position: absolute;
    left: 40px;
    right: 30px;
    bottom: 34px;
    display: flex;
    align-items: center;
    justify-content: space-between;
    font-size: 17px;
    font-weight: 500;
  }
  .contact-item {
    display: flex;
    align-items: center;
    gap: 8px;
  }
  .contact-item svg { flex: none; }
  .address {
    font-size: 11.5px;
    line-height: 15px;
    font-weight: 500;
  }
</style>
</head>
<body>
  <main class="letterhead">
    <svg class="header-sweep" viewBox="0 0 640 270" aria-hidden="true">
      <defs>
        <linearGradient id="sweepRed" x1="0" y1="1" x2="1" y2="0">
          <stop offset="0" stop-color="var(--red-bright)"/>
          <stop offset="0.45" stop-color="#c8141f"/>
          <stop offset="1" stop-color="var(--red-deep)"/>
        </linearGradient>
      </defs>
      <path d="M0 0 H610 C380 40 150 110 30 270 L0 270 Z" fill="url(#sweepRed)"/>
      <path d="M640 14 C400 50 170 125 62 270" fill="none" stroke="var(--navy)" stroke-width="5"/>
    </svg>

    <div class="brand">
      <span class="brand-mark"></span>
      <span class="brand-name">Marwick Law</span>
    </div>

    <div class="recipient">
      Mr/s<br>
      First Name and Last Name<br>
      Company Name<br>
      Address
    </div>

    <section class="letter-body">
      <p>Lorem ipsum dolor sit amet,consectetur adipiscing sed do eiusmod tempor incididunt laboreet dolore magna aliqua.Ut enim ad minim.veniam, quis nostrud exercitation ullamco laboris nisi ut aliquip exea commodo consequat.Lorem ipsum dolor sit amet,consectetur adipiscing sed do eiusmod tempor incididunt.labore et dolore magna aliqua. Ut enim</p>
      <p>Lorem ipsum dolor sit amet, consectetur adipiscing sed do eiusmod tempor incididunt labore et dolore magna aliqua. Ut enim ad minim veniam, quis nostrud exercitation ullamco laboris nisi ut aliquip exea commodo consequat.Duis aute irure dolor in reprehenderit in voluptate velit esse cillum irure dolor in reprehenderit in voluptate velit esse irure</p>
      <p>Lorem ipsum dolor sit amet, consectetur adipiscing sed do eiusmod tempor incididunt labore et dolore magna aliqua. consequat. Duis aute irure dolor in.reprehenderit in voluptate velit esse cillum dolore eu fugiat nulla pariatur. Excepteur sint occaecat cupidatat non proident, sunt in culpa qui officia deserunt mollit,</p>
      <p>Lorem ipsum dolor sit amet, consectetur adipiscing sed do eiusmod tempor incididunt labore et dolore magna aliqua. Ut enim Lorem ipsum dolor sit amet, consectetur adipiscing sed do eiusmod tempor incididunt labore et dolore magna aliqua. Ut enim Lorem ipsum aliqua.ipsum</p>
      <p>Lorem ipsum dolor sit amet, consectetur adipiscing sed do eiusmod tempor incididunt labore et dolore magna aliqua. Ut enim ad minim veniam, quis nostrud exercitation ullamco laboris nisi ut aliquip exea commodo consequat.Duis aute irure dolor in reprehenderit in voluptate velit esse cillum irure dolor in reprehenderit in voluptate velit esse irure</p>
      <p>Lorem ipsum dolor sit amet, consectetur adipiscing sed do eiusmod tempor incididunt labore et dolore magna aliqua. Ut enim ad minim veniam, quis nostrud exercitation ullamco laboris nisi ut aliquip exea commodo consequat.Duis aute irure dolor in reprehenderit in voluptate velit esse cillum irure dolor in reprehenderit in voluptate velit esse irure</p>
    </section>

    <div class="closing">
      Regards
      <span class="signature" role="img" aria-label="Handwritten signature"></span>
    </div>

    <footer class="contact-bar">
      <div class="contact-item">
        <svg width="26" height="22" viewBox="0 0 26 22" aria-hidden="true">
          <path d="M2 14 Q13 4 24 14 L21 19 L17 16 L17 13 Q13 11 9 13 L9 16 L5 19 Z" fill="var(--red-bright)"/>
          <path d="M6 8 Q13 2 20 8" fill="none" stroke="var(--red-bright)" stroke-width="2"/>
        </svg>
        <span>832-361-9027</span>
      </div>
      <div class="contact-item">
        <svg width="24" height="24" viewBox="0 0 24 24" aria-hidden="true">
          <rect x="6" y="2" width="12" height="6" fill="var(--red-deep)"/>
          <rect x="2" y="8" width="20" height="10" rx="2" fill="var(--red-bright)"/>
          <rect x="6" y="14" width="12" height="8" fill="#fff" stroke="var(--red-bright)" stroke-width="1.5"/>
          <line x1="8" y1="17" x2="16" y2="17" stroke="var(--red-bright)"/>
          <line x1="8" y1="19.5" x2="16" y2="19.5" stroke="var(--red-bright)"/>
        </svg>
        <span>832-614-7359</span>
      </div>
      <div class="contact-item">
        <svg width="20" height="26" viewBox="0 0 20 26" aria-hidden="true">
          <path d="M10 25 L3 14 A8 8 0 1 1 17 14 Z" fill="var(--red-bright)"/>
          <circle cx="10" cy="9" r="3.5" fill="#fff"/>
        </svg>
        <span class="address">1475 Calloway Street,<br>Suite 210, Houston,<br>Texas 77041</span>
      </div>
    </footer>
  </main>
</body>
</html>
```